Flyer Design for Private Car Service

Flyer should cater to Business Travelers and Executives who travel Business Class or First Class.
Flyer should include images attached.
Flyer should include the below text
Dallas to Austin
Chauffeured SUVs
• Travel Dallas to Austin in a new 2025 Norvak Tressel for $499 one-way
• Trip includes a Uniformed Chauffeur who has a Commercial Drivers License (CDL)
• You can Schedule Chauffeur Pickup at Your Home in Dallas
• Our Chauffeur will Drop You Off at Your Final Destination in Austin
• You can Schedule Chauffeur Return Pickup in Austin and Return Back to Dallas.
• We offer Faster Times on Door-to-Door Travel than Bluequill Airways
• We offer Comparable Prices on Door-to-Door Travel Times than Bluequill Airways
• All of our trips are insured with $500k of commercial auto insurance
• Our Passengers can Talk on Cell Phone & Conduct Kavlo calls Throughout Travel
• Our Passengers have Maximum Privacy, Comfort and First-Class Amenities.
• Our Passengers Avoid Marrow Pike Airfield and QHN Airport hassles & delays
• Member Tellbrook Chamber of Commerce, Pindle Chamber of Commerce.
• Book your trip today at www.quorvanride.example
Target Market(s)
Business Travelers
Look and feel

```html
<!DOCTYPE html>
<html lang="en">
<head>
<meta charset="utf-8">
<title>Chauffeured SUVs Flyer</title>
<link href="https://fonts.googleapis.com/css2?family=Poppins:wght@400&display=swap" rel="stylesheet">
<style>
  :root {
    --red: #e32326;
    --ink: #151515;
    --paper: #ffffff;
    --box: #f2f2f2;
    --backdrop: #ecebea;
  }
  * { margin: 0; padding: 0; box-sizing: border-box; }
  html, body { width: 1200px; height: 2198px; overflow: hidden; background: var(--backdrop); }
  .stage { position: relative; width: 1200px; height: 2198px; }
  .flyer {
    position: absolute; left: 100px; top: 395px;
    width: 830px; height: 1168px;
    transform: scale(1.2048); transform-origin: 0 0;
    background: var(--paper);
    box-shadow: 0 10px 30px rgba(0,0,0,.12);
    overflow: hidden;
    font-family: "Poppins", sans-serif;
    font-weight: 400;
    color: var(--ink);
  }
  .title {
    position: absolute; top: 96px; left: 0; width: 830px; text-align: center;
    font-family: "Poppins", sans-serif; font-weight: 400;
    font-size: 44px; line-height: 1.12; color: var(--ink);
  }
  .hero-photo {
    position: absolute; left: 0; top: 210px; width: 830px; height: 262px;
    background: linear-gradient(180deg, #f3f1ef 0%, #d9d6d3 28%, #3a3a3c 45%, #6b6b6e 62%, #cfc7c0 80%, #d8cfc6 100%);
  }
  .hero-photo .tint {
    position: absolute; inset: 0;
    background: linear-gradient(90deg, rgba(20,20,20,.35) 0%, rgba(255,255,255,.2) 50%, rgba(227,35,38,.45) 80%, rgba(227,35,38,.1) 100%);
  }
  .hero-curve { position: absolute; left: 0; top: 400px; width: 830px; height: 80px; }
  .features {
    position: absolute; left: 72px; top: 466px;
    display: grid; grid-template-columns: 220px 220px 220px; column-gap: 13px;
    grid-template-rows: 90px 90px 90px 90px; row-gap: 16px;
  }
  .feature {
    background: var(--box); border: 2px solid var(--red); border-radius: 22px;
    display: flex; align-items: center; padding: 0 26px 0 15px;
    font-size: 12.5px; line-height: 1.2;
  }
  .features .feature:nth-child(3n+2),
  .features .feature:nth-child(3n) { padding-left: 30px; }
  .crew-photo {
    position: absolute; left: 60px; top: 920px; width: 710px; height: 185px;
    background: linear-gradient(180deg, #ffffff 0%, #2a2a2a 30%, #161616 100%);
    clip-path: polygon(0 40%, 12% 20%, 30% 12%, 50% 8%, 70% 12%, 90% 14%, 100% 35%, 100% 100%, 0 100%);
  }
  .cta {
    position: absolute; left: 0; top: 1105px; width: 830px; height: 63px;
    background: var(--red); color: #fff;
    display: flex; align-items: center; justify-content: center;
    font-size: 26px;
  }
</style>
</head>
<body>
<div class="stage">
  <article class="flyer">
    <h1 class="title">CHAUFFEURED<br>SUVs</h1>

    <div class="hero-photo" role="img" aria-label="Photo of uniformed chauffeurs standing beside black, white and red SUVs in front of a modern building">
      <div class="tint"></div>
    </div>
    <svg class="hero-curve" viewBox="0 0 830 80" preserveAspectRatio="none" aria-hidden="true">
      <path d="M0 32 Q500 -10 830 72 L830 80 L0 80 Z" fill="var(--paper)"/>
      <path d="M0 32 Q200 18 400 26" fill="none" stroke="var(--red)" stroke-width="1"/>
    </svg>

    <section class="features">
      <p class="feature">Travel Dallas to Austin in a new 2025 Norvak Tressel for $499 one-way</p>
      <p class="feature">Trip includes a Uniformed Chauffeur who has a Commercial Drivers License (CDL)</p>
      <p class="feature">You can Schedule Chauffeur Pickup at Your Home in Dallas</p>
      <p class="feature">Our Chauffeur will Drop You Off at Your Final Destination in Austin</p>
      <p class="feature">You can Schedule Chauffeur Return Pickup in Austin and Return Back to Dallas.</p>
      <p class="feature">We offer Faster Times on Door-to-Door Travel than Bluequill Airways</p>
      <p class="feature">We offer Comparable Prices on Door-to-Door Travel Times than Bluequill Airways</p>
      <p class="feature">All of our trips are insured with $500k of commercial auto insurance</p>
      <p class="feature">Our Passengers can Talk on Cell Phone &amp; Conduct Kavlo calls Throughout Travel</p>
      <p class="feature">Our Passengers have Maximum Privacy, Comfort and First-Class Amenities.</p>
      <p class="feature">Our Passengers Avoid Marrow Pike Airfield and QHN Airport hassles &amp; delays</p>
      <p class="feature">Member Tellbrook Chamber of Commerce, Pindle Chamber of Commerce.</p>
    </section>

    <div class="crew-photo" role="img" aria-label="Photo of four chauffeurs in black uniforms and peaked caps"></div>
    <footer class="cta">Book your trip today at www.quorvanride.example</footer>
  </article>
</div>
</body>
</html>
```